Business Card Design Project

We are a construction company in Orange County, CA. We need a two sided business card. We would like the back to be our logo with web URL. Front should included Name, title, address, phone, fax and email address.

our address is
627 West Dorrance Blvd, Suite 308
Anaheim, CA 92718

Our logo files are attached.

Construction

```html
<!DOCTYPE html>
<html lang="en">
<head>
<meta charset="utf-8">
<title>Torveld Business Card</title>
<link rel="stylesheet" href="https://fonts.googleapis.com/css2?family=Open+Sans:wght@400;700;800&display=swap">
<style>
  :root {
    --brand-blue: #1d4a7c;
    --ink-grey: #5a5a5a;
    --tab-grey: #5f5f5f;
    --card-white: #ffffff;
    --backdrop: #e4e4e4;
  }
  * { margin: 0; padding: 0; box-sizing: border-box; }
  html, body { width: 1200px; height: 402px; overflow: hidden; }
  body {
    background: var(--backdrop);
    font-family: "Open Sans", Arial, sans-serif;
    position: relative;
  }
  .card {
    position: absolute;
    top: 56px;
    width: 512px;
    height: 291px;
    background: var(--card-white);
  }
  .card--front { left: 58px; }
  .card--back { left: 630px; }

  .brand-name {
    position: absolute;
    font-weight: 800;
    color: var(--brand-blue);
    letter-spacing: 1px;
    line-height: 1;
    white-space: nowrap;
  }
  .card--front .brand-name { left: 38px; top: 28px; font-size: 66px; }
  .card--back .brand-name {
    left: 0; right: 0; top: 110px;
    text-align: center; font-size: 66px;
  }

  .edge-tab {
    position: absolute;
    width: 7px;
  }
  .edge-tab--left {
    left: -1px; top: 146px; height: 126px;
    background: var(--brand-blue);
    border-radius: 0 5px 5px 0;
  }
  .edge-tab--right {
    right: -1px; top: 178px; height: 62px;
    background: var(--tab-grey);
    border-radius: 5px 0 0 5px;
  }

  .contact-list {
    position: absolute;
    left: 30px; top: 158px;
    list-style: none;
    font-size: 13px;
    color: var(--ink-grey);
  }
  .contact-list li {
    display: flex;
    align-items: center;
    height: 16px;
  }
  .contact-list svg {
    width: 11px; height: 11px;
    margin-right: 5px;
    fill: var(--brand-blue);
  }
  .address {
    position: absolute;
    left: 30px; top: 232px;
    font-size: 13px;
    line-height: 17px;
    color: var(--ink-grey);
    font-style: normal;
  }
  .person {
    position: absolute;
    right: 29px; top: 192px;
    text-align: right;
    color: var(--ink-grey);
  }
  .person__name { font-size: 16px; font-weight: 700; line-height: 20px; }
  .person__title { font-size: 13px; line-height: 18px; }
</style>
</head>
<body>
  <section class="card card--front" aria-label="Card front">
    <div class="brand-name">TORVELD</div>
    <span class="edge-tab edge-tab--left"></span>
    <span class="edge-tab edge-tab--right"></span>

    <ul class="contact-list">
      <li>
        <svg viewBox="0 0 12 12" aria-hidden="true"><circle cx="6" cy="6" r="6"/><path d="M4 3h1.3l.6 1.6-.8.6a4 4 0 0 0 1.7 1.7l.6-.8 1.6.6V8a1 1 0 0 1-1 1A5 5 0 0 1 3 4a1 1 0 0 1 1-1z" fill="#fff"/></svg>
        01-555-0142
      </li>
      <li>
        <svg viewBox="0 0 12 12" aria-hidden="true"><rect x="3" y="1" width="6" height="3"/><rect x="0.5" y="4.5" width="11" height="5" rx="1"/><rect x="3" y="8" width="6" height="3.5"/></svg>
        01-555-0187
      </li>
      <li>
        <svg viewBox="0 0 12 12" aria-hidden="true"><rect x="0.5" y="2.5" width="11" height="7.5"/><path d="M0.5 2.5 6 7l5.5-4.5" fill="none" stroke="#fff" stroke-width="1"/></svg>
        hello@torveldbuild.com
      </li>
      <li>
        <svg viewBox="0 0 12 12" aria-hidden="true"><circle cx="6" cy="6" r="5.5"/><path d="M0.5 6h11M6 0.5c-2.5 3-2.5 8 0 11M6 0.5c2.5 3 2.5 8 0 11" fill="none" stroke="#fff" stroke-width="0.8"/></svg>
        www.torveldbuild.com
      </li>
    </ul>

    <address class="address">
      627 West Dorrance Blvd<br>
      Suite 308 Anaheim, CA 92718
    </address>

    <div class="person">
      <div class="person__name">Your name</div>
      <div class="person__title">Title</div>
    </div>
  </section>

  <section class="card card--back" aria-label="Card back">
    <div class="brand-name">TORVELD</div>
  </section>
</body>
</html>
```